iPhone iOS 7 App For Managing Tasks/Photos for Internal Company Use

We need an app design that displays company objectives and task, and provides the interface for employees to complete a task by uploading a photo and adding comments.

Please see attached mock up sketches as a rough guideline

Final delivery of files must contain PSD, and all layers/objects sliced both is PSD and PNG files

Target Market(s)

This is a tool for internal employee use

Industry/Entity Type

It Company

Requirements
Must have
• Must include logo, and match the colour scheme
Use iPhone iOS 7 Style

```html
<!DOCTYPE html>
<html lang="en">
<head>
<meta charset="utf-8">
<title>Select On Objective</title>
<link rel="stylesheet" href="https://fonts.googleapis.com/css2?family=Arimo:wght@400;700&display=swap">
<style>
  :root {
    --status-top: #e4e6e8;
    --status-bottom: #a9adb2;
    --header-top: #2b4a86;
    --header-bottom: #0c1f4a;
    --water-top: #1f5f86;
    --water-mid: #154a6c;
    --water-bottom: #0b2a42;
    --row-bg: rgba(10, 40, 70, 0.78);
    --row-edge: rgba(120, 170, 210, 0.35);
    --text: #ffffff;
    --star-on: #f5b400;
    --star-off: #c7ccd2;
    --btn-top: #d9dcdf;
    --btn-bottom: #80858b;
    --tab-top: #2a2a2a;
    --tab-bottom: #050505;
    --orange: #f58a1f;
    --red: #e0202a;
    --blue: #2f8fe0;
    --green: #5cb83a;
  }
  * { box-sizing: border-box; margin: 0; padding: 0; }
  html, body { width: 800px; height: 1200px; overflow: hidden; }
  body { font-family: "Arimo", Arial, sans-serif; color: var(--text); }
  .screen {
    position: relative; width: 800px; height: 1200px; overflow: hidden;
  }
  .backdrop {
    position: absolute; inset: 0;
    background: radial-gradient(ellipse at 60% 35%, var(--water-top), var(--water-mid) 55%, var(--water-bottom));
  }
  .status-bar {
    position: absolute; top: 0; left: 0; width: 800px; height: 50px;
    background: linear-gradient(var(--status-top), var(--status-bottom));
    color: #222; font-weight: 700; font-size: 32px;
    display: flex; align-items: center; justify-content: center;
  }
  .status-bar .signal { position: absolute; left: 18px; top: 14px; }
  .status-bar .battery { position: absolute; right: 16px; top: 14px; }
  .title-bar {
    position: absolute; top: 50px; left: 0; width: 800px; height: 100px;
    background: linear-gradient(var(--header-top), var(--header-bottom));
    display: flex; align-items: center; justify-content: center;
    font-weight: 700; font-size: 40px;
  }
  .refresh {
    position: absolute; left: 35px; top: 18px; width: 90px; height: 66px;
    border-radius: 10px; border: 2px solid #8a99b5;
    background: linear-gradient(#f2f4f7, #9ea8b6);
    display: flex; align-items: center; justify-content: center;
  }
  .task {
    position: absolute; left: 38px; width: 724px; height: 143px;
    background: var(--row-bg); border-top: 2px solid var(--row-edge);
  }
  .task .icon {
    position: absolute; left: 8px; top: 16px; width: 110px; height: 110px;
    border-radius: 18px; display: flex; align-items: center; justify-content: center;
  }
  .task .summary {
    position: absolute; left: 118px; top: 6px; width: 520px;
    font-weight: 700; font-size: 30px; line-height: 38px;
  }
  .task .rating {
    position: absolute; left: 118px; top: 96px;
    display: flex; align-items: center; gap: 3px; font-size: 26px;
  }
  .task .count { margin-left: 18px; }
  .view-btn {
    position: absolute; right: 8px; top: 30px; width: 104px; height: 55px;
    border-radius: 6px; background: linear-gradient(var(--btn-top), var(--btn-bottom));
    color: #fff; font-weight: 700; font-size: 24px;
    display: flex; align-items: center; justify-content: center;
  }
  .tab-bar {
    position: absolute; left: 0; bottom: 0; width: 800px; height: 150px;
    background: linear-gradient(var(--tab-top), var(--tab-bottom));
    display: flex; justify-content: space-around; align-items: flex-start;
  }
  .tab { width: 180px; display: flex; flex-direction: column; align-items: center; padding-top: 10px; }
  .tab .tab-icon {
    width: 90px; height: 90px; border-radius: 14px;
    display: flex; align-items: center; justify-content: center;
  }
  .tab .label { font-weight: 700; font-size: 28px; margin-top: 8px; }
</style>
</head>
<body>
<main class="screen">
  <div class="backdrop" role="img" aria-label="Blue water background photograph"></div>

  <div class="status-bar">
    <svg class="signal" width="70" height="22" viewBox="0 0 70 22"><rect x="0" y="16" width="8" height="6" fill="#222"/><rect x="12" y="12" width="8" height="10" fill="#222"/><rect x="24" y="8" width="8" height="14" fill="#222"/><rect x="36" y="4" width="8" height="18" fill="#222"/><rect x="48" y="0" width="8" height="22" fill="#222"/></svg>
    <span class="time">9:20 AM</span>
    <svg class="battery" width="54" height="24" viewBox="0 0 54 24"><rect x="1" y="1" width="46" height="22" rx="3" fill="none" stroke="#222" stroke-width="2"/><rect x="5" y="5" width="38" height="14" fill="#222"/><rect x="48" y="7" width="5" height="10" fill="#222"/></svg>
  </div>

  <header class="title-bar">
    <div class="refresh">
      <svg width="40" height="40" viewBox="0 0 40 40"><path d="M30 12 A13 13 0 1 0 33 24" fill="none" stroke="#1d2f55" stroke-width="5"/><path d="M24 4 L34 12 L22 16 Z" fill="#1d2f55"/></svg>
    </div>
    <h1 style="font-size:40px">Select On Objective</h1>
  </header>

  <section class="task" style="top:155px">
    <div class="icon" style="background:#c9ccd0">
      <svg width="80" height="80" viewBox="0 0 80 80"><rect x="8" y="8" width="64" height="64" rx="10" fill="var(--red)"/><rect x="22" y="22" width="36" height="36" rx="4" fill="#fff"/></svg>
    </div>
    <p class="summary">Lorem ipsum dolor sit amet, cons ectetur adipisicing.</p>
    <div class="rating">
      <svg width="170" height="28" viewBox="0 0 170 28"><g id="s"><polygon points="14,1 18,10 27,10 20,16 23,26 14,20 5,26 8,16 1,10 10,10" fill="var(--star-on)"/></g><use href="#s" x="34"/><use href="#s" x="68"/><polygon transform="translate(102 0)" points="14,1 18,10 27,10 20,16 23,26 14,20 5,26 8,16 1,10 10,10" fill="var(--star-off)"/><polygon transform="translate(136 0)" points="14,1 18,10 27,10 20,16 23,26 14,20 5,26 8,16 1,10 10,10" fill="var(--star-off)"/></svg>
      <span class="count">( 7</span>
    </div>
    <div class="view-btn">View</div>
  </section>

  <section class="task" style="top:330px">
    <div class="icon" style="background:var(--orange)">
      <svg width="70" height="70" viewBox="0 0 70 70"><g transform="rotate(-40 35 35)"><rect x="27" y="6" width="16" height="44" rx="3" fill="#fff"/><polygon points="27,50 43,50 35,64" fill="#fff"/></g></svg>
    </div>
    <p class="summary">Lorem ipsum dolor sit amet, cons ectetur adipisicing.</p>
    <div class="rating">
      <svg width="170" height="28" viewBox="0 0 170 28"><use href="#s"/><use href="#s" x="34"/><use href="#s" x="68"/><use href="#s" x="102"/><polygon transform="translate(136 0)" points="14,1 18,10 27,10 20,16 23,26 14,20 5,26 8,16 1,10 10,10" fill="var(--star-off)"/></svg>
      <span class="count">( 5</span>
    </div>
    <div class="view-btn">View</div>
  </section>

  <section class="task" style="top:508px">
    <div class="icon" style="background:var(--red)">
      <svg width="70" height="70" viewBox="0 0 70 70" fill="#fff"><rect x="6" y="6" width="16" height="16"/><rect x="27" y="6" width="16" height="16"/><rect x="48" y="6" width="16" height="16"/><rect x="6" y="27" width="16" height="16"/><rect x="27" y="27" width="16" height="16"/><rect x="48" y="27" width="16" height="16"/><rect x="6" y="48" width="16" height="16"/><rect x="27" y="48" width="16" height="16"/></svg>
    </div>
    <p class="summary">Lorem ipsum dolor sit amet, cons ectetur adipisicing.</p>
    <div class="rating">
      <svg width="170" height="28" viewBox="0 0 170 28"><use href="#s"/><use href="#s" x="34"/><use href="#s" x="68"/><polygon transform="translate(102 0)" points="14,1 18,10 27,10 20,16 23,26 14,20 5,26 8,16 1,10 10,10" fill="var(--star-off)"/><polygon transform="translate(136 0)" points="14,1 18,10 27,10 20,16 23,26 14,20 5,26 8,16 1,10 10,10" fill="var(--star-off)"/></svg>
      <span class="count">( 6</span>
    </div>
    <div class="view-btn">View</div>
  </section>

  <section class="task" style="top:688px">
    <div class="icon" style="background:var(--blue)">
      <svg width="72" height="72" viewBox="0 0 72 72"><g fill="#fff"><circle cx="36" cy="36" r="22"/><rect x="30" y="4" width="12" height="64" rx="2"/><rect x="4" y="30" width="64" height="12" rx="2"/><rect x="30" y="4" width="12" height="64" rx="2" transform="rotate(45 36 36)"/><rect x="30" y="4" width="12" height="64" rx="2" transform="rotate(-45 36 36)"/></g><circle cx="36" cy="36" r="9" fill="var(--blue)"/></svg>
    </div>
    <p class="summary">Lorem ipsum dolor sit amet, cons ectetur adipisicing.</p>
    <div class="rating">
      <svg width="170" height="28" viewBox="0 0 170 28"><use href="#s"/><use href="#s" x="34"/><use href="#s" x="68"/><use href="#s" x="102"/><use href="#s" x="136"/></svg>
      <span class="count">( 9</span>
    </div>
    <div class="view-btn">View</div>
  </section>

  <section class="task" style="top:862px">
    <div class="icon" style="background:var(--green)">
      <svg width="70" height="70" viewBox="0 0 70 70"><rect x="18" y="4" width="34" height="62" rx="6" fill="#fff"/><rect x="23" y="12" width="24" height="42" fill="var(--green)"/><circle cx="35" cy="60" r="3" fill="var(--green)"/></svg>
    </div>
    <p class="summary">Lorem ipsum dolor sit amet, cons ectetur adipisicing.</p>
    <div class="rating">
      <svg width="170" height="28" viewBox="0 0 170 28"><use href="#s"/><use href="#s" x="34"/><use href="#s" x="68"/><use href="#s" x="102"/><polygon transform="translate(136 0)" points="14,1 18,10 27,10 20,16 23,26 14,20 5,26 8,16 1,10 10,10" fill="var(--star-off)"/></svg>
      <span class="count">( 5</span>
    </div>
    <div class="view-btn">View</div>
  </section>

  <nav class="tab-bar">
    <div class="tab">
      <div class="tab-icon" style="background:linear-gradient(#ff9a2e,#d85a06)">
        <svg width="60" height="60" viewBox="0 0 60 60"><polygon points="30,6 56,30 48,30 48,54 12,54 12,30 4,30" fill="#fff"/><rect x="24" y="36" width="12" height="18" fill="#d85a06"/></svg>
      </div>
      <span class="label">Home</span>
    </div>
    <div class="tab">
      <div class="tab-icon" style="background:linear-gradient(#6a2a1c,#2a0d08)">
        <svg width="68" height="68" viewBox="0 0 68 68"><circle cx="34" cy="34" r="28" fill="#fff"/><circle cx="34" cy="34" r="21" fill="var(--red)"/><circle cx="34" cy="34" r="14" fill="#fff"/><circle cx="34" cy="34" r="7" fill="var(--red)"/></svg>
      </div>
      <span class="label">Objective</span>
    </div>
    <div class="tab">
      <div class="tab-icon" style="background:linear-gradient(#2c3e78,#0a1233);border:2px solid #c0c6d6">
        <svg width="66" height="66" viewBox="0 0 66 66"><circle cx="33" cy="28" r="20" fill="#2f8fe0" stroke="#fff" stroke-width="2"/><ellipse cx="33" cy="28" rx="9" ry="20" fill="none" stroke="#fff" stroke-width="2"/><line x1="13" y1="28" x2="53" y2="28" stroke="#fff" stroke-width="2"/><text x="33" y="62" fill="#fff" font-size="10" font-family="Arimo, sans-serif" text-anchor="middle">News</text></svg>
      </div>
      <span class="label">News</span>
    </div>
    <div class="tab">
      <div class="tab-icon" style="background:linear-gradient(#ff3a3a,#b80c0c)">
        <svg width="60" height="60" viewBox="0 0 60 60"><path d="M19 16 A18 18 0 1 0 41 16" fill="none" stroke="#fff" stroke-width="6" stroke-linecap="round"/><line x1="30" y1="6" x2="30" y2="30" stroke="#fff" stroke-width="6" stroke-linecap="round"/></svg>
      </div>
      <span class="label">Logout</span>
    </div>
  </nav>
</main>
</body>
</html>
```